Real Estate Media Company Business Card

’m looking for a modern, high-end, double-sided business card for:
Bright Harbor Studios LLC
(Real Estate Photography & Videography)
The design should feel clean, minimal, and premium, appealing to top real estate agents and brokers.
👉 Horizontal layout is preferred
👉 Vertical option is welcome but not required
⸻
Front Side (Main Information):
Include:
* Desmond Whitfield
* Bright Harbor Studios LLC
* Title (open to creative improvement)
* Phone Number
* Email
* Website
⸻
Services Section (VERY IMPORTANT):
This should be a key visual element, not an afterthought.
Services to Include:
* Cinematic Video
* Real Estate Photography
* Drone
* Social Media Reels
* Floor Plans
* Use clean, modern icons next to each service
* Icons should be simple, minimal, and consistent style (outline or thin line preferred)
* Option to place icons inside small circles (like reference)
Layout:
* Format services similar to a clean horizontal or grid-style list (like “example 2”)
* Keep spacing balanced and uncluttered
* Make this section visually appealing and easy to scan
⸻
Back Side:
* Keep it extremely minimal
* Only include the logo in a corner
* No additional text needed
⸻
Typography & Style:
* Modern, clean, slightly bold fonts (based on uploaded references)
* Strong hierarchy (name + services stand out most)
* Plenty of white/negative space
* Avoid clutter
⸻
Overall Feel:
* Luxury
* Modern
* Clean
* Confident
* High-end real estate branding
⸻
Notes for Designers:
* Simplicity is key
* Services section should feel polished and intentional
* This card should feel like something a top-producing real estate agent would keep
Target Market(s)
Real estate agent agents

```html
<!DOCTYPE html>
<html lang="en">
<head>
<meta charset="utf-8">
<title>Bright Harbor Studios – Business Card</title>
<link href="https://fonts.googleapis.com/css2?family=Ubuntu:wght@400;500&display=swap" rel="stylesheet">
<style>
  :root {
    --page: #3b352d;
    --card: #121212;
    --ink: #f2f2f2;
    --ink-soft: #e4e4e4;
    --metal-light: #a9a7a8;
    --metal-dark: #6f6d6e;
  }
  * { margin: 0; padding: 0; box-sizing: border-box; }
  html, body {
    width: 1060px; height: 1200px; overflow: hidden;
    background: var(--page);
    font-family: "Ubuntu", sans-serif;
    color: var(--ink);
  }
  .card {
    position: absolute; left: 160px; width: 740px; height: 422px;
    background: var(--card); border-radius: 21px; overflow: hidden;
  }
  .card--front { top: 109px; }
  .card--back { top: 619px; }

  .identity { position: absolute; left: 37px; top: 32px; }
  .identity__name { font-size: 41px; font-weight: 500; line-height: 1.15; letter-spacing: 0.3px; }
  .identity__title { font-size: 25px; font-weight: 400; line-height: 1.3; margin-top: 2px; }
  .identity__company { font-size: 28px; font-weight: 500; line-height: 1.3; margin-top: 4px; }

  .services-divider {
    position: absolute; left: 357px; top: 157px; width: 3px; height: 159px; background: var(--ink);
  }
  .services { position: absolute; left: 381px; top: 149px; list-style: none; }
  .services__item { display: flex; align-items: center; height: 35.3px; font-size: 24px; letter-spacing: 0.4px; }
  .services__icon { width: 33px; height: 22px; margin-right: 14px; flex: none; }

  .contact { position: absolute; left: 37px; top: 309px; list-style: none; }
  .contact__item { display: flex; align-items: center; height: 32px; font-size: 20px; letter-spacing: 0.3px; color: var(--ink-soft); }
  .contact__icon { width: 22px; height: 22px; margin-right: 12px; flex: none; }

  .back__surface {
    position: absolute; left: 0; top: 0; width: 100%; height: 253px;
    background: linear-gradient(170deg, var(--metal-dark) 0%, var(--metal-light) 55%, #8f8d8e 100%);
  }
  .back__band { position: absolute; left: 0; top: 253px; width: 100%; height: 169px; background: var(--card); }
  .back__mark {
    position: absolute; left: 571px; top: 292px; transform: translate(-50%, -50%);
    display: flex; align-items: center; gap: 10px;
    font-size: 19px; font-weight: 400; letter-spacing: 2px; white-space: nowrap; color: var(--ink);
  }
  .back__mark-square { width: 12px; height: 12px; background: var(--ink); }
</style>
</head>
<body>
<svg width="0" height="0" style="position:absolute">
  <symbol id="icon-camera" viewBox="0 0 33 22">
    <g fill="none" stroke="currentColor" stroke-width="1.3">
      <rect x="1" y="4" width="31" height="17" rx="1.5"/>
      <path d="M11 4 L13 1 H20 L22 4"/>
      <circle cx="16.5" cy="12.5" r="5.5"/>
      <circle cx="16.5" cy="12.5" r="3.3"/>
      <path d="M3 2.5 H8"/>
      <rect x="26" y="6.5" width="3" height="2"/>
    </g>
  </symbol>
</svg>

<section class="card card--front">
  <header class="identity">
    <h1 class="identity__name">Desmond Whitfield</h1>
    <p class="identity__title">Founder | Real Estate Media Specialist</p>
    <p class="identity__company">Bright Harbor Studios LLC</p>
  </header>

  <div class="services-divider"></div>
  <ul class="services">
    <li class="services__item"><svg class="services__icon"><use href="#icon-camera"/></svg>Cinematic Video</li>
    <li class="services__item"><svg class="services__icon"><use href="#icon-camera"/></svg>Real Estate Photography</li>
    <li class="services__item"><svg class="services__icon"><use href="#icon-camera"/></svg>Drone</li>
    <li class="services__item"><svg class="services__icon"><use href="#icon-camera"/></svg>Social Media Reels</li>
    <li class="services__item"><svg class="services__icon"><use href="#icon-camera"/></svg>Floor Plans</li>
  </ul>

  <ul class="contact">
    <li class="contact__item">
      <svg class="contact__icon" viewBox="0 0 24 24"><path fill="currentColor" d="M6.6 10.8a15.1 15.1 0 0 0 6.6 6.6l2.2-2.2a1 1 0 0 1 1-.25 11.4 11.4 0 0 0 3.6.57 1 1 0 0 1 1 1V20a1 1 0 0 1-1 1A17 17 0 0 1 3 4a1 1 0 0 1 1-1h3.5a1 1 0 0 1 1 1c0 1.25.2 2.45.57 3.57a1 1 0 0 1-.25 1z"/></svg>
      555-014-2287
    </li>
    <li class="contact__item">
      <svg class="contact__icon" viewBox="0 0 24 24"><path fill="currentColor" d="M2 5h20v14H2z M4 7.2v.3l8 5 8-5v-.3z" fill-rule="evenodd"/></svg>
      desmond@brightharborstudios.com
    </li>
    <li class="contact__item">
      <svg class="contact__icon" viewBox="0 0 24 24"><g fill="none" stroke="currentColor" stroke-width="1.5"><circle cx="12" cy="12" r="10"/><ellipse cx="12" cy="12" rx="4.5" ry="10"/><path d="M2 12h20M4 6.5h16M4 17.5h16M12 2v20"/></g></svg>
      www.brightharborstudios.com
    </li>
  </ul>
</section>

<section class="card card--back">
  <div class="back__surface" role="img" aria-label="Brushed silver metallic texture"></div>
  <div class="back__band"></div>
  <div class="back__mark"><span class="back__mark-square"></span>BRIGHT HARBOR STUDIOS</div>
</section>
</body>
</html>
```